Mission Statement Board for front lobby

We need a mission statement board for our front lobby at our company called TrellisWorks. We are a web content management company that builds websites for our clients. We would like two boards, same size, canvas material (not thin poster board or anything like that) size H 3' x L 2', white background, blue and black colored font, our logo on top in blue/gray/black and some blue coloring around top and bottom, kind of framing the white background. Please reference our very rough draft we did in Word so you get an idea of what we're thinking- the attachment shows what we would like on each board. Reference our website to see logo and fonts if you would like, please keep the board similar to our fonts and colors. www.trellisworks-example.com

Contact info: Marta Kowalczyk
Email: marta.kowalczyk@trellisworks-example.com
Phone: 555-207-3948
Updates

Please do not include in a design my contact info, no email marta.kowalczyk@trellisworks-example.com, no phone # 555-207-3948. I added that info to the project when I posted it, but it is not part of the design.... reference attachment posted in project with exactly what we want.

Target Market(s)

Clients & employees in the office who will see the boards in lobby

Industry/Entity Type

It Company

Font styles to use
Other font styles liked:
• reference attachment (but font is flexible within reason)

Colors
33a6d7
0255a3
eaf1f7
0292cd
85cae6
cee9f5
000000
5c5c5c
959595

Requirements
Must have
• Needs to be a professional sign that hangs on wall, company logo, cohesive colors and fonts
Nice to have
• Get creative with the border/framing around the white background
Should not have
• Unprofessional fonts, typos, thin cheap looking poster board materal.

```html
<!DOCTYPE html>
<html lang="en">
<head>
<meta charset="utf-8">
<title>TrellisWorks Lobby Boards</title>
<link rel="stylesheet" href="https://fonts.googleapis.com/css2?family=Montserrat:wght@400;600;700&family=Raleway:wght@300;400&display=swap">
<style>
  :root {
    --navy: #0a2a6b;
    --blue-deep: #0255a3;
    --blue: #0292cd;
    --blue-mid: #33a6d7;
    --blue-light: #85cae6;
    --blue-pale: #cee9f5;
    --mist: #eaf1f7;
    --ink: #1a1a1a;
    --grey-dark: #5c5c5c;
    --grey: #959595;
    --heading: #0b3b7d;
    --backdrop: #f6f1d6;
  }
  * { margin: 0; padding: 0; box-sizing: border-box; }
  html, body { width: 1200px; height: 857px; overflow: hidden; }
  body {
    background: var(--backdrop);
    position: relative;
    font-family: "Raleway", sans-serif;
  }
  .board {
    position: absolute;
    top: 28px;
    width: 537px;
    height: 803px;
    overflow: hidden;
    background: radial-gradient(ellipse at center, #ffffff 0%, #f7f9fb 70%, var(--mist) 100%);
  }
  .board--mission { left: 41px; }
  .board--values { left: 617px; }

  .band { position: absolute; left: 0; right: 0; }
  .band--top { top: 0; height: 96px; }
  .band--bottom { bottom: 0; height: 96px; }
  .band__stripe { display: block; width: 100%; }
  .stripe--navy { height: 40px; background: var(--navy); }
  .stripe--blue { height: 28px; background: var(--blue-deep); }
  .stripe--sky { height: 20px; background: linear-gradient(90deg, var(--blue-light), var(--blue-mid)); }
  .stripe--silver { height: 8px; background: linear-gradient(90deg, #c9ced6, #f4f6f8 40%, #959595 100%); }

  .block { position: absolute; left: 0; right: 0; text-align: center; }

  .brand {
    top: 176px;
    display: flex;
    justify-content: center;
    align-items: center;
    gap: 10px;
  }
  .brand__dot { width: 26px; height: 26px; border-radius: 50%; background: var(--blue-deep); }
  .brand__name {
    font-family: "Montserrat", sans-serif;
    font-weight: 700;
    font-size: 30px;
    color: var(--blue-deep);
    letter-spacing: 0.5px;
  }

  .heading {
    font-family: "Montserrat", sans-serif;
    font-weight: 700;
    color: var(--heading);
    line-height: 1;
  }
  .heading--large { font-size: 31px; }
  .lead {
    font-weight: 400;
    font-size: 22px;
    line-height: 30px;
    color: var(--ink);
    padding: 0 50px;
    text-align: justify;
    text-align-last: center;
  }

  .mission-title { top: 302px; }
  .mission-text { top: 346px; }
  .faith-title { top: 485px; }
  .faith-text { top: 528px; }

  .values-title { top: 270px; }
  .value { position: absolute; left: 0; right: 0; text-align: center; padding: 0 50px; }
  .value__name {
    font-family: "Montserrat", sans-serif;
    font-weight: 600;
    font-size: 17px;
    color: var(--heading);
    line-height: 20px;
  }
  .value__text {
    font-size: 14px;
    line-height: 19px;
    color: var(--ink);
    margin-top: 1px;
  }
  .value--integrity { top: 314px; }
  .value--accountability { top: 388px; }
  .value--respect { top: 444px; }
  .value--excellence { top: 519px; }
  .value--loyalty { top: 593px; }
</style>
</head>
<body>

<section class="board board--mission">
  <div class="band band--top" aria-hidden="true">
    <span class="band__stripe stripe--navy"></span>
    <span class="band__stripe stripe--blue"></span>
    <span class="band__stripe stripe--sky"></span>
    <span class="band__stripe stripe--silver"></span>
  </div>

  <div class="block brand">
    <span class="brand__dot"></span>
    <span class="brand__name">TrellisWorks</span>
  </div>

  <h2 class="block heading heading--large mission-title">OUR MISSION STATEMENT:</h2>
  <p class="block lead mission-text">We design and implement extraordinary web solutions to help our clients achieve their goals.</p>

  <h2 class="block heading heading--large faith-title">OUR FAITH...</h2>
  <p class="block lead faith-text">We reflect the love of Christ in us and through us to our fellow employees, partners and clients.</p>

  <div class="band band--bottom" aria-hidden="true">
    <span class="band__stripe stripe--silver"></span>
    <span class="band__stripe stripe--sky"></span>
    <span class="band__stripe stripe--blue"></span>
    <span class="band__stripe stripe--navy"></span>
  </div>
</section>

<section class="board board--values">
  <div class="band band--top" aria-hidden="true">
    <span class="band__stripe stripe--navy"></span>
    <span class="band__stripe stripe--blue"></span>
    <span class="band__stripe stripe--sky"></span>
    <span class="band__stripe stripe--silver"></span>
  </div>

  <div class="block brand">
    <span class="brand__dot"></span>
    <span class="brand__name">TrellisWorks</span>
  </div>

  <h2 class="block heading heading--large values-title">OUR CORE VALUES</h2>

  <div class="value value--integrity">
    <h3 class="value__name">INTEGRITY</h3>
    <p class="value__text">We believe that to be successful, it is essential to operate at the highest levels of honesty, responsibility and trust.</p>
  </div>
  <div class="value value--accountability">
    <h3 class="value__name">ACCOUNTABILITY</h3>
    <p class="value__text">Taking responsibility for one’s own actions.</p>
  </div>
  <div class="value value--respect">
    <h3 class="value__name">RESPECT</h3>
    <p class="value__text">Understand and value differences in others.<br>Listen thoughtfully to understand.</p>
  </div>
  <div class="value value--excellence">
    <h3 class="value__name">EXCELLENCE</h3>
    <p class="value__text">We continually improve our standards and processes so that excellence simply becomes a natural consequence of our work.</p>
  </div>
  <div class="value value--loyalty">
    <h3 class="value__name">LOYALTY</h3>
    <p class="value__text">Working collaboratively with TrellisWorks employees, partners and customers to solve problems and achieve goals.</p>
  </div>

  <div class="band band--bottom" aria-hidden="true">
    <span class="band__stripe stripe--silver"></span>
    <span class="band__stripe stripe--sky"></span>
    <span class="band__stripe stripe--blue"></span>
    <span class="band__stripe stripe--navy"></span>
  </div>
</section>

</body>
</html>
```